Business Card - connecting 2 souls and beggining the journey of self discovery

Logo on the front
with tag line

On the back list of services and contact details

Seminars
workshops
Coaching
podcasts

Darren Whitlow
Health & Wellbeing Life Coach
0491 372 615
darren@brightcoreliving.example
brightcoreliving.example

Industry/Entity Type

Life Coaching

Contact Information for Business Card

I like the use of colour from the logo to be used. I'm not a fan of white.

Requirements
Must have
• My tagline: The path inward begins with you
Nice to have
• Use of colour that is in the mind body soul logo

```html
<!DOCTYPE html>
<html lang="en">
<head>
<meta charset="utf-8">
<title>Brightcore Living – Business Card</title>
<link rel="stylesheet" href="https://fonts.googleapis.com/css2?family=Questrial&family=Open+Sans:wght@400;700&display=swap">
<style>
  :root{
    --backdrop:#222325;
    --card:#ffffff;
    --ink:#3a3a3c;
    --brand-grey:#8a8a8c;
    --accent:#f2566a;
    --purple:#7d4fa6;
    --magenta:#b0549a;
    --orange:#f27c58;
    --amber:#e9a752;
    --green:#7cc05a;
  }
  *{margin:0;padding:0;box-sizing:border-box}
  html,body{width:1200px;height:1000px;overflow:hidden}
  body{background:var(--backdrop);position:relative;font-family:"Open Sans",Arial,sans-serif;color:var(--ink)}
  .card{position:absolute;left:290px;width:620px;height:354px;background:var(--card);border-radius:28px;overflow:hidden;box-shadow:0 18px 40px rgba(0,0,0,.45)}
  .card--front{top:116px}
  .card--back{top:530px}

  /* front */
  .front-mark{position:absolute;left:0;right:0;top:118px;display:flex;align-items:center;justify-content:center;gap:16px}
  .mark-dot{width:54px;height:54px;border-radius:50%;background:var(--orange)}
  .brand-name{font-family:"Questrial",Arial,sans-serif;font-size:34px;color:var(--brand-grey);letter-spacing:-.5px}
  .tagline{position:absolute;left:0;right:0;bottom:44px;text-align:center;font-size:13px;letter-spacing:3.2px;text-transform:uppercase;color:var(--accent)}

  /* back */
  .colour-band{position:absolute;left:0;top:0;bottom:0;width:118px;background:linear-gradient(180deg,var(--purple) 0%,var(--magenta) 22%,var(--orange) 52%,var(--amber) 76%,var(--green) 100%)}
  .band-dot{position:absolute;left:70px;top:104px;width:96px;height:96px;border-radius:50%;background:var(--card);border:5px solid var(--card);box-shadow:0 0 0 3px rgba(125,79,166,.25)}
  .back-brand{position:absolute;right:34px;top:30px;font-family:"Questrial",Arial,sans-serif;font-size:30px;color:var(--brand-grey);letter-spacing:-.5px}
  .services{position:absolute;right:34px;top:118px;text-align:right;font-size:14px;line-height:1.4;color:var(--ink)}
  .person{position:absolute;left:190px;top:156px}
  .person__name{font-size:22px;font-weight:700;text-transform:uppercase;letter-spacing:.3px;color:var(--ink);line-height:1.1}
  .person__role{font-size:17px;color:var(--accent);margin-top:2px}
  .contacts{position:absolute;left:190px;top:232px;list-style:none;font-size:15px;line-height:1.5}
  .contacts li{display:flex;align-items:center;gap:10px}
  .contacts svg{width:13px;height:13px;flex:none}
  .contacts .web-host{color:var(--accent)}
</style>
</head>
<body>

<section class="card card--front" aria-label="Card front">
  <div class="front-mark">
    <span class="mark-dot" aria-hidden="true"></span>
    <span class="brand-name">Brightcore Living</span>
  </div>
  <p class="tagline">The path inward begins with you</p>
</section>

<section class="card card--back" aria-label="Card back">
  <div class="colour-band" aria-hidden="true"></div>
  <span class="band-dot" aria-hidden="true"></span>
  <p class="back-brand">Brightcore Living</p>
  <p class="services">Seminars | Workshops<br>Coaching | Podcasts</p>

  <div class="person">
    <p class="person__name">Darren Whitlow</p>
    <p class="person__role">Life Coach</p>
  </div>

  <ul class="contacts">
    <li>
      <svg viewBox="0 0 12 12" aria-hidden="true"><rect x="3" y="0.8" width="6" height="10.4" rx="1.2" fill="none" stroke="var(--accent)" stroke-width="1.3"/><circle cx="6" cy="9.3" r=".7" fill="var(--accent)"/></svg>
      0491 372 615
    </li>
    <li>
      <svg viewBox="0 0 12 12" aria-hidden="true"><rect x="0.8" y="2.3" width="10.4" height="7.4" rx=".8" fill="var(--accent)"/><path d="M1 2.8 6 6.6 11 2.8" fill="none" stroke="#fff" stroke-width="1"/></svg>
      darren@brightcoreliving.example
    </li>
    <li>
      <svg viewBox="0 0 12 12" aria-hidden="true"><circle cx="6" cy="6" r="5.2" fill="var(--accent)"/><path d="M.8 6h10.4M6 .8c-2.2 2.8-2.2 7.6 0 10.4M6 .8c2.2 2.8 2.2 7.6 0 10.4" fill="none" stroke="#fff" stroke-width=".8"/></svg>
      <span>www.<span class="web-host">brightcoreliving.example</span></span>
    </li>
  </ul>
</section>

</body>
</html>
```